Verpackungen für Shampoos
Zielgruppe
Wir sind ein kleines Familienunternehmen mit 2-3 Friseurfilialen und Onlineshop im Naturfriseurbereich, arbeiten mit ökologischen, nachhaltigen und natürlichen Produkten und vertreiben unsere eigene Haarbürste. Wir betreiben mit Sol Verde unsere eigene Marke in diesem Bereich. Erste Produkte, wie eine eigene Haarbürste sind bereits vorhanden und entstanden.
Für unsere erste Shampoo Serie suchen wir ein klares, cleanes und hochwertiges Design. Die 200ml Shampooflasche kommt komplett in weiß und besteh aus recyceltem Material. Es soll klar die ökologisch nachhaltige und etwas höherpreisige Marke kommuniziert werden. Dabei sehen wir vom Stil „weniger ist mehr“ als ganz klare Designvorgabe. Anbei auch ein Beispiel von Pavura, die das ganze sehr schön umgesetzt haben.
Die INCI sind noch nicht final. Es wäre schön, wenn hier ein Platzhalter eingefügt würde. Da eine der Hauptzielgruppen auch Österreicher sind, würden wir uns über ein kleines „Made in Austria“ auf der Vorderseite (evtl. ganz unten auf der Flasche) freuen.
Insgesamt sind es vier verschiedene Shampoos, die aus der gleichen Serie stammen. Es wäre schön, wenn man diese auch direkt unterscheiden könnte. Vielleicht durch ein grafisches Element, oder einfach nur durch die verschiedenen Namenserweiterungen. Hier die Aufstellung mit den Erweiterungen:
Es werden 4 verschiedene Shampoos, die Namen sind:
Revive - Strapaziertes Haar
Pure - Normales Haar
Sensitiv - Empfindliche Kopfhaut
Balancing - Fettiges Haar
Zielgruppe:
Weiblich, 30-60 Jahre, mittleres bis gehobenes Einkommen, nachhaltig, ökologisch, natürlich, legt Wert auf hochwertige Produkte und Dienstleistungen, achtet auf Konsum.
Aufgabenstellung
Die Landingpage zur Bürste ist hier erreichbar (Beispiel):
Vielleicht hilft das etwas um das Design und die Tonality aufzuschnappen: https://sol-verde.de/gold-birch-wildschweinborstenbuerste/
Es wäre super, wenn das Design der Flasche ähnlich klar und strukturiert ist.
Die Shampoos sind komplett vegan und made in Austria. Die beiden Aspekte sollten in Design auch aufgegriffen werden. Da wir einen 4 farbigen Tamponade/Siebdruck auf der Flasche anwenden, stehen leider nicht so viele Farben zur Verfügung (3-4).
Link zur Flasche:
https://www.brumoxa.com/de/kosmetik/varleno/varleno-tubica/flasche-heavy-200ml-24-410-plastik
Des Weiteren kann sich noch am Sol Verde Haarkonzept und unserem Dienstleistungsflyer orientiert werden.
Benefits:
-       Pflegt das Haar, hält es geschmeidig
- Bio Shampoo Konzentrat
-       Die Grundlage für gesunde Kopfhaut und schönes Haar*
-       Vermindert Spliss*
-       Hält die Haare natürlich geschmeidig
-       Regt die Durchblutung der Kopfhaut an
-       Verteilt Nährstoffe von der Wurzel bis in die Spitzen*
-       Verbessert das Kopfhautklima*
-       Für eine gut durchblutete und gesunde Kopfhaut mit glänzenden und
geschmeidigen Haaren*
-       Entfernt Schuppen und abgestorbene Hautpartikel
-       Verbessert natürlich die allgemeine Haarstruktur
-       Entwirrt langes und gelocktes Haar
-       Reinigt die Kopfhaut ohne Chemie*
-       Mehr Volumen im Haar
-       Mehr Stand im Haar durch Kräftigung der Haarbalkmuskulatur
-       Spart Shampoo und hilft Shampoo seltener und weniger zu nutzen
-       Nährstoffversorgung bis in die Haarspitzen
Inhaltsstoffe:
Pure
Aloe Vera Direktsaft*, Decyl Glucoside, Coco Glucoside, Lauryl Glucoside, Hopfenextrakt*, Pentylene Glycol green, Meli..

```html
<!DOCTYPE html>
<html lang="de">
<head>
<meta charset="UTF-8">
<title>Sol Verde – Shampoo Revive</title>
<link href="https://fonts.googleapis.com/css2?family=Montserrat:wght@400;500;700&display=swap" rel="stylesheet">
<style>
  :root {
    --stage: #d9d9d9;
    --bottle: #ffffff;
    --cap: #f2f2f2;
    --cap-edge: #e2e2e2;
    --sage: #94b38f;
    --sage-light: #a9c4a3;
    --ink: #1f1f1f;
    --ink-soft: #4a4a4a;
  }
  * { margin: 0; padding: 0; box-sizing: border-box; }
  html, body { width: 1200px; height: 1200px; overflow: hidden; }
  body {
    background: var(--stage);
    font-family: "Montserrat", sans-serif;
    color: var(--ink);
    position: relative;
  }
  .bottle {
    position: absolute;
    width: 224px;
    background: var(--bottle);
  }
  .bottle--back { left: 314px; top: 120px; height: 935px; }
  .bottle--front { left: 585px; top: 183px; height: 928px; }
  .bottle__cap {
    position: absolute;
    top: 0; left: 0; right: 0;
    height: 152px;
    background: var(--cap);
    border-bottom: 2px solid var(--cap-edge);
  }
  .bottle__band {
    position: absolute;
    top: -3px;
    left: 63px;
    width: 97px;
    height: 196px;
    background: linear-gradient(160deg, var(--sage-light), var(--sage));
  }
  .brand {
    position: absolute;
    left: 0; right: 0;
    text-align: center;
    font-weight: 400;
    color: var(--ink);
  }
  .brand--front { top: 426px; font-size: 22px; letter-spacing: 0.02em; }
  .brand--back { top: 765px; font-size: 7px; }
  .product-name {
    position: absolute;
    top: 601px;
    left: 0; right: 0;
    text-align: center;
    font-weight: 700;
    font-size: 14px;
    line-height: 1.45;
    letter-spacing: 0.03em;
  }
  .claim-badge {
    position: absolute;
    top: 722px;
    left: 80px;
    width: 64px;
    height: 64px;
  }
  .claim-badge text {
    font-family: "Montserrat", sans-serif;
    font-size: 7px;
    font-weight: 500;
    fill: var(--ink);
  }
  .origin {
    position: absolute;
    top: 851px;
    left: 0; right: 0;
    text-align: center;
    font-size: 7.5px;
    font-weight: 500;
    letter-spacing: 0.2em;
  }
  .ingredients {
    position: absolute;
    top: 798px;
    left: 10px; right: 10px;
    text-align: center;
    font-size: 8.5px;
    line-height: 1.4;
    color: var(--ink-soft);
  }
  .ingredients__title { margin-bottom: 14px; }
  .ingredients__variant { margin-bottom: 1px; }
</style>
</head>
<body>

  <section class="bottle bottle--back" aria-label="Flaschenrückseite">
    <div class="bottle__cap"></div>
    <div class="bottle__band" role="img" aria-label="Salbeigrünes Banderolenfeld mit zarter Pinselstruktur"></div>
    <p class="brand brand--back">Sol Verde</p>
    <div class="ingredients">
      <p class="ingredients__title">Inhaltsstoffe:</p>
      <p class="ingredients__variant">Pure</p>
      <p>Aloe Vera Direktsaft*, Decyl Glucoside, Coco Glucoside, Lauryl Glucoside, Hopfenextrakt*, Pentylene Glycol green, Melissenblätter-Extrakt*, Arganöl*, Brokkolisamenöl*, Xanthan Gum, Parfümöl natürlich 'Maiglöckchen'</p>
    </div>
  </section>

  <section class="bottle bottle--front" aria-label="Flaschenvorderseite">
    <div class="bottle__cap"></div>
    <div class="bottle__band" role="img" aria-label="Salbeigrünes Banderolenfeld mit zarter Pinselstruktur"></div>
    <p class="brand brand--front">Sol Verde</p>
    <h1 class="product-name">REVIVE<br>STRAPAZIERTES HAAR</h1>
    <svg class="claim-badge" viewBox="0 0 64 64" aria-label="100% Recycelt, Vegan">
      <defs>
        <path id="badge-ring" d="M32,32 m-22,0 a22,22 0 1,1 44,0 a22,22 0 1,1 -44,0"/>
      </defs>
      <text><textPath href="#badge-ring" textLength="134" lengthAdjust="spacing">100% RECYCELT · VEGAN ·</textPath></text>
      <circle cx="32" cy="32" r="2.5" fill="var(--ink)"/>
    </svg>
    <p class="origin">MADE IN AUSTRIA</p>
  </section>

</body>
</html>
```